Family history tech product tailored for moms needs banner ads

none (button has no web address) is launching next week and we've partnered with an ad group that will be launching a campaign on school district websites that will be pushed to 250k moms of school age children.

We're launching a $199 product that shows you more about who you are through your family's history. We connect people wanting to learn more about themselves with expert researcher/genealogist who will uncover their past and find the stories of their ancestors.

See branding guidelines below as well as the landing page we're designing where these ads will take you.

Here is the landing page design:
https://files.quellbox-share.com/Q93KD8R71-P2ZXW4KL8-ab12cd34ef

Target Market(s)

Mom's of kids in elementary and middle school.

Persona:
Mom, 38 years old, 2 kids (age 6 and 8)
Lives in Dallas, drives a 2016 Norvik Stallard
She and husband met in college. She was a nurse, but she stopped working to be a full-time mom
Husband is in financial consulting, household income of $140,000
When kids at school, she runs errands, works out, meets up with girlfriends for coffee
She shops at Fernabelle, has active hobbies
She is always busy, there’s not enough time for her family; she is worried that her kids may become distant because of how busy the family is
She values time with family most, soccer weekends, financial stability, college for the kids
Wants to connect more with the kids and the family to increase the bond, and she thinking having more context for the family will help them bond around a common history
Her objections to Kethra are lack of trust in a new service, time it will cost her to get the info she wants to achieve her goals

Industry/Entity Type

Startup

Other font styles liked:
• follow style guide

Requirements
Must have
• Must follow the design pattern in our branding guide.
• https://www.stashpail.com/s/qk7m2x9vbn4wtr8/Capture%202016-11-30%2013.39.48.png?dl=0
Nice to have
• Good copy, I'm less worried about that though. We can work together on that.
Should not have
• Stock imagery that sucks. I'm really opposed to anything that looks like it is from the 2001 - 2011

```html
<!DOCTYPE html>
<html lang="en">
<head>
<meta charset="utf-8">
<title>Kethra – Everyone has a story</title>
<link href="https://fonts.googleapis.com/css2?family=Open+Sans:wght@700&display=swap" rel="stylesheet">
<style>
  :root {
    --ink-slate: #3c5a73;
    --brand-teal: #17989f;
    --brand-blue: #3aa0ef;
    --button-navy: #243746;
    --paper: #ffffff;
    --mist-blue: #e3effb;
    --deep-teal-1: #0e5f6e;
    --deep-teal-2: #137485;
    --deep-teal-3: #0b4c5a;
  }
  html, body {
    margin: 0;
    padding: 0;
    overflow: hidden;
    background: var(--paper);
  }
  .banner {
    position: relative;
    width: 1200px;
    height: 500px;
    overflow: hidden;
    font-family: "Open Sans", Arial, sans-serif;
    background: var(--paper);
  }
  .banner__backdrop {
    position: absolute;
    inset: 0;
  }
  .brand {
    position: absolute;
    left: 522px;
    top: 20px;
    display: flex;
    align-items: center;
    gap: 14px;
    color: var(--brand-blue);
    font-weight: 700;
    font-size: 50px;
    line-height: 1;
  }
  .brand__dot {
    width: 40px;
    height: 40px;
    border-radius: 50%;
    background: var(--brand-blue);
  }
  .headline {
    position: absolute;
    left: 108px;
    top: 142px;
    margin: 0;
  }
  .headline__lead {
    display: block;
    margin-left: 70px;
    color: var(--ink-slate);
    font-weight: 700;
    font-size: 47px;
    line-height: 1.1;
    letter-spacing: -0.3px;
  }
  .headline__punch {
    display: block;
    color: var(--brand-teal);
    font-weight: 700;
    font-size: 90px;
    line-height: 1.05;
    letter-spacing: -1px;
  }
  .cta {
    position: absolute;
    left: 151px;
    top: 344px;
    width: 383px;
    height: 92px;
    display: flex;
    align-items: center;
    justify-content: center;
    background: var(--button-navy);
    color: var(--paper);
    font-weight: 700;
    font-size: 52px;
    letter-spacing: -0.5px;
    cursor: pointer;
  }
</style>
</head>
<body>
  <div class="banner">
    <svg class="banner__backdrop" width="1200" height="500" viewBox="0 0 1200 500">
      <defs>
        <linearGradient id="facetedTeal" x1="0" y1="0" x2="1" y2="1">
          <stop offset="0" stop-color="var(--deep-teal-3)"/>
          <stop offset="0.5" stop-color="var(--deep-teal-2)"/>
          <stop offset="1" stop-color="var(--deep-teal-1)"/>
        </linearGradient>
        <linearGradient id="mistFade" x1="0" y1="0" x2="1" y2="0">
          <stop offset="0" stop-color="var(--mist-blue)" stop-opacity="0.9"/>
          <stop offset="0.7" stop-color="var(--mist-blue)" stop-opacity="0.25"/>
          <stop offset="1" stop-color="var(--mist-blue)" stop-opacity="0"/>
        </linearGradient>
      </defs>
      <rect class="backdrop__facets" x="0" y="0" width="1200" height="500" fill="url(#facetedTeal)" role="img" aria-label="Deep teal low-poly faceted texture"/>
      <ellipse class="backdrop__light-arc" cx="320" cy="120" rx="445" ry="460" fill="var(--paper)"/>
      <rect x="0" y="0" width="250" height="500" fill="var(--paper)"/>
      <rect class="backdrop__streaks" x="0" y="0" width="520" height="500" fill="url(#mistFade)" role="img" aria-label="Faint light-blue diagonal streak pattern"/>
    </svg>

    <div class="brand">
      <span class="brand__dot"></span>
      <span class="brand__name">Kethra</span>
    </div>

    <h1 class="headline">
      <span class="headline__lead">Everyone has a story...</span>
      <span class="headline__punch">Find yours.</span>
    </h1>

    <div class="cta" role="button">Learn More</div>
  </div>
</body>
</html>
```